New Zealand Marlborough Sauvignon Blanc wine packaging design

We need packaging design for our new wine brand, Dunmore Vale. The wine is a New Zealand Marlborough Sauvignon Blanc. We would like the packaging will portray elegance and style with an understated label. We are looking for a label that portrays the elegance of the French Riviera. The label should be round or pill shaped.
Updates

Industry/Entity Type

Wine

Font styles to use
Serif
Sans Serif

Requirements
Must have
• The words in order of importance: Dunmore Vale, Sauvignon Blanc, Marlborough, New Zealand. It should be fit to the bottle posted in the links
Nice to have
• a pill shape or circular shape
Should not have
• Illustrations of wine bottles, wine glasses, or grapes

```html
<!DOCTYPE html>
<html lang="en">
<head>
<meta charset="utf-8">
<title>Dunmore Vale — Sauvignon Blanc label variants</title>
<link rel="stylesheet" href="https://fonts.googleapis.com/css2?family=Almendra+SC&family=Open+Sans:wght@400&display=swap">
<style>
  :root {
    --backdrop-light: #e6e6e6;
    --backdrop-dark: #d6d6d6;

    --mono-paper: #ffffff;
    --mono-ink: #1b1b1b;

    --night-paper: #1e1e1e;
    --night-ink: #ffffff;

    --blush-paper: #fffdf0;
    --blush-ring: #e2c8ce;
    --blush-ink: #4d4d4d;
    --blush-art-a: #e4c9d0;
    --blush-art-b: #d2b1bb;

    --copper-paper: #fdf7f3;
    --copper-ink: #6b2a1a;
    --copper-art-a: #f7ddd2;
    --copper-art-b: #d9ad98;

    --display-font: "Almendra SC", Georgia, serif;
    --body-font: "Open Sans", Arial, sans-serif;
  }

  * { margin: 0; padding: 0; box-sizing: border-box; }

  html, body {
    width: 1200px;
    height: 989px;
    overflow: hidden;
  }

  body {
    background: radial-gradient(ellipse at 40% 40%, var(--backdrop-light), var(--backdrop-dark));
  }

  .label-board {
    position: relative;
    width: 1200px;
    height: 989px;
  }

  .wine-label {
    position: absolute;
    width: 426px;
    height: 426px;
    filter: drop-shadow(0 2px 3px rgba(0,0,0,0.12));
  }
  .wine-label--mono   { left: 36px;  top: 36px; }
  .wine-label--night  { left: 523px; top: 36px; }
  .wine-label--blush  { left: 36px;  top: 520px; }
  .wine-label--copper { left: 523px; top: 520px; }

  .brand-name {
    font-family: var(--display-font);
    font-size: 44px;
    letter-spacing: 1px;
  }
  .varietal {
    font-family: var(--display-font);
    font-size: 23px;
    letter-spacing: 1px;
  }
  .region {
    font-family: var(--body-font);
    font-size: 17px;
    letter-spacing: 1px;
  }

  .wine-label--mono .paper   { fill: var(--mono-paper); stroke: var(--mono-ink); stroke-width: 3; }
  .wine-label--mono .inner-ring { fill: none; stroke: var(--mono-ink); stroke-width: 1; }
  .wine-label--mono text     { fill: var(--mono-ink); }

  .wine-label--night .paper  { fill: var(--night-paper); stroke: var(--night-paper); stroke-width: 3; }
  .wine-label--night .inner-ring { fill: none; stroke: var(--night-ink); stroke-width: 1; }
  .wine-label--night text    { fill: var(--night-ink); }

  .wine-label--blush .paper  { fill: var(--blush-paper); stroke: var(--blush-ring); stroke-width: 5; }
  .wine-label--blush .inner-ring { fill: none; stroke: var(--blush-ring); stroke-width: 1; }
  .wine-label--blush text    { fill: var(--blush-ink); }

  .wine-label--copper .paper { fill: var(--copper-paper); stroke: var(--copper-ink); stroke-width: 3; }
  .wine-label--copper .inner-ring { fill: none; stroke: var(--copper-ink); stroke-width: 1; }
  .wine-label--copper text   { fill: var(--copper-ink); }
</style>
</head>
<body>
<main class="label-board">

  <!-- White label, black ink -->
  <svg class="wine-label wine-label--mono" viewBox="0 0 426 426" aria-label="Dunmore Vale Sauvignon Blanc label, white">
    <defs>
      <path id="mono-top-arc" d="M 48 213 A 165 165 0 0 1 378 213"/>
      <path id="mono-bottom-arc" d="M 30 213 A 183 183 0 0 0 396 213"/>
    </defs>
    <circle class="paper" cx="213" cy="213" r="211"/>
    <circle class="inner-ring" cx="213" cy="213" r="204"/>
    <text class="brand-name"><textPath href="#mono-top-arc" startOffset="50%" text-anchor="middle">Dunmore Vale</textPath></text>
    <circle class="rose-art" cx="215" cy="220" r="122" fill="var(--mono-ink)" role="img" aria-label="Woodcut illustration of a rose wreathed in leaves"/>
    <text class="region" transform="translate(41 240) rotate(90)" text-anchor="middle">Marlborough</text>
    <text class="region" transform="translate(390 240) rotate(-90)" text-anchor="middle">New Zealand</text>
    <text class="varietal"><textPath href="#mono-bottom-arc" startOffset="50%" text-anchor="middle">Sauvignon Blanc</textPath></text>
  </svg>

  <!-- Black label, white ink -->
  <svg class="wine-label wine-label--night" viewBox="0 0 426 426" aria-label="Dunmore Vale Sauvignon Blanc label, black">
    <defs>
      <path id="night-top-arc" d="M 48 213 A 165 165 0 0 1 378 213"/>
      <path id="night-bottom-arc" d="M 30 213 A 183 183 0 0 0 396 213"/>
    </defs>
    <circle class="paper" cx="213" cy="213" r="211"/>
    <circle class="inner-ring" cx="213" cy="213" r="204"/>
    <text class="brand-name"><textPath href="#night-top-arc" startOffset="50%" text-anchor="middle">Dunmore Vale</textPath></text>
    <circle class="rose-art" cx="215" cy="220" r="122" fill="var(--night-ink)" role="img" aria-label="Woodcut illustration of a rose wreathed in leaves, white on black"/>
    <text class="region" transform="translate(41 240) rotate(90)" text-anchor="middle">Marlborough</text>
    <text class="region" transform="translate(390 240) rotate(-90)" text-anchor="middle">New Zealand</text>
    <text class="varietal"><textPath href="#night-bottom-arc" startOffset="50%" text-anchor="middle">Sauvignon Blanc</textPath></text>
  </svg>

  <!-- Cream label, blush rose -->
  <svg class="wine-label wine-label--blush" viewBox="0 0 426 426" aria-label="Dunmore Vale Sauvignon Blanc label, cream and blush">
    <defs>
      <path id="blush-top-arc" d="M 48 213 A 165 165 0 0 1 378 213"/>
      <path id="blush-bottom-arc" d="M 30 213 A 183 183 0 0 0 396 213"/>
      <radialGradient id="blush-art-tone" cx="50%" cy="45%" r="60%">
        <stop offset="0" stop-color="var(--blush-art-b)"/>
        <stop offset="1" stop-color="var(--blush-art-a)"/>
      </radialGradient>
    </defs>
    <circle class="paper" cx="213" cy="213" r="210"/>
    <circle class="inner-ring" cx="213" cy="213" r="204"/>
    <text class="brand-name"><textPath href="#blush-top-arc" startOffset="50%" text-anchor="middle">Dunmore Vale</textPath></text>
    <circle class="rose-art" cx="215" cy="220" r="122" fill="url(#blush-art-tone)" role="img" aria-label="Woodcut illustration of a rose wreathed in leaves, soft pink"/>
    <text class="region" transform="translate(41 240) rotate(90)" text-anchor="middle">Marlborough</text>
    <text class="region" transform="translate(390 240) rotate(-90)" text-anchor="middle">New Zealand</text>
    <text class="varietal"><textPath href="#blush-bottom-arc" startOffset="50%" text-anchor="middle">Sauvignon Blanc</textPath></text>
  </svg>

  <!-- Ivory label, copper ink -->
  <svg class="wine-label wine-label--copper" viewBox="0 0 426 426" aria-label="Dunmore Vale Sauvignon Blanc label, ivory and copper">
    <defs>
      <path id="copper-top-arc" d="M 48 213 A 165 165 0 0 1 378 213"/>
      <path id="copper-bottom-arc" d="M 30 213 A 183 183 0 0 0 396 213"/>
      <linearGradient id="copper-art-tone" x1="0" y1="0" x2="1" y2="1">
        <stop offset="0" stop-color="var(--copper-art-a)"/>
        <stop offset="1" stop-color="var(--copper-art-b)"/>
      </linearGradient>
    </defs>
    <circle class="paper" cx="213" cy="213" r="211"/>
    <circle class="inner-ring" cx="213" cy="213" r="204"/>
    <text class="brand-name"><textPath href="#copper-top-arc" startOffset="50%" text-anchor="middle">Dunmore Vale</textPath></text>
    <circle class="rose-art" cx="215" cy="220" r="122" fill="url(#copper-art-tone)" role="img" aria-label="Woodcut illustration of a rose wreathed in leaves, peach to copper"/>
    <text class="region" transform="translate(41 240) rotate(90)" text-anchor="middle">Marlborough</text>
    <text class="region" transform="translate(390 240) rotate(-90)" text-anchor="middle">New Zealand</text>
    <text class="varietal"><textPath href="#copper-bottom-arc" startOffset="50%" text-anchor="middle">Sauvignon Blanc</textPath></text>
  </svg>

</main>
</body>
</html>
```